Stationery Design Project

Need stationery designed for our chicken farming business. We grow chickens in barns for meat production. Looking for all stationery items (business cards, letterhead, envelopes, with compliments etc).

Reason: I am going away for 5 days from Friday 30/3/2012. Won't be able to check designs.

Target Market(s)

The stationery will only be used for correspondence with key stakeholders / suppliers. It is not to be used for marketing etc.

Industry/Entity Type

Business

Requirements
Must have
• I have included all the contact details required for each type of stationery.
Nice to have
• Colours to be used white, green, red, yellow and black (see design).
Should not have
• Rounded Corners.
Centralised information (in centre of business cards / letterhead etc).

```html
<!DOCTYPE html>
<html lang="en">
<head>
<meta charset="utf-8">
<title>Brookvale Poultry – Stationery Set</title>
<link href="https://fonts.googleapis.com/css2?family=Josefin+Sans:wght@300;400;600&family=Arimo&display=swap" rel="stylesheet">
<style>
  :root{
    --green-dark:#2e6a4c;
    --green-mid:#3f8660;
    --green-light:#64a985;
    --red:#b8312f;
    --ink:#2b2b2b;
    --grey-text:#8a8a8a;
    --paper:#ffffff;
    --stage:#f1f1f1;
    --band:#2a2a2a;
  }
  *{box-sizing:border-box;margin:0;padding:0}
  html,body{width:1200px;height:895px;overflow:hidden}
  body{
    position:relative;
    background:radial-gradient(ellipse at 60% 40%, #ffffff 0%, var(--stage) 55%, #e4e4e4 100%);
    font-family:"Josefin Sans", sans-serif;
    color:var(--ink);
  }
  .piece{position:absolute;background:var(--paper);box-shadow:0 6px 14px rgba(0,0,0,.18);overflow:hidden}
  .wave{position:absolute;left:0;bottom:0;width:100%}

  /* brand name lockup */
  .brand{position:absolute;display:flex;align-items:center;gap:6px;white-space:nowrap}
  .brand-dot{border-radius:50%;background:var(--red);flex:none}
  .brand-name{font-family:"Josefin Sans", sans-serif;font-weight:600;color:var(--green-dark);line-height:1}

  /* business card front */
  .card-front{left:38px;top:60px;width:311px;height:169px}
  .card-front .brand{left:0;width:100%;justify-content:center;top:60px}
  .card-front .brand-dot{width:18px;height:18px}
  .card-front .brand-name{font-size:15px}

  /* business card back */
  .card-back{left:417px;top:64px;width:310px;height:171px;background:var(--green-dark);color:#fff}
  .card-back .brand{right:16px;top:24px}
  .card-back .brand-dot{width:10px;height:10px;background:#fff}
  .card-back .brand-name{font-size:9px;color:#fff}
  .holder-name{position:absolute;left:23px;top:36px;font-size:15px;font-weight:300}
  .holder-role{position:absolute;left:96px;top:57px;font-size:10px;font-weight:300}
  .card-address{position:absolute;left:32px;top:112px;font-size:6px;font-weight:300;line-height:8px}
  .card-address .label{font-size:8px}
  .card-divider{position:absolute;left:154px;top:101px;width:1px;height:57px;background:#fff}
  .card-contact{position:absolute;left:168px;top:110px;font-size:7.5px;font-weight:300;line-height:9px}

  /* disc */
  .disc{position:absolute;left:797px;top:152px;width:368px;height:368px;border-radius:50%;background:var(--paper);box-shadow:0 6px 14px rgba(0,0,0,.18);overflow:hidden}
  .disc .brand{left:0;width:100%;justify-content:center;top:62px}
  .disc .brand-dot{width:20px;height:20px}
  .disc .brand-name{font-size:15px}
  .disc-hole{position:absolute;left:148px;top:148px;width:72px;height:72px;border-radius:50%;background:#efefef;box-shadow:inset 0 0 0 10px #f7f7f7}
  .disc-topic{position:absolute;left:0;width:100%;text-align:center;top:304px;font-size:20px;font-weight:300;color:#fff}

  /* letterhead */
  .letterhead{left:66px;top:343px;width:362px;height:469px}
  .letterhead .brand{left:0;width:100%;justify-content:center;top:38px}
  .letterhead .brand-dot{width:14px;height:14px}
  .letterhead .brand-name{font-size:12px}
  .header-rule{position:absolute;left:0;top:84px;width:100%;height:1px;background:#777}
  .letter-date{position:absolute;right:16px;top:105px;font-size:11px;font-weight:300;color:#555}
  .letter-body{position:absolute;left:50px;top:130px;width:250px;font-family:"Arimo", sans-serif;font-size:5.6px;line-height:8px;color:var(--grey-text)}
  .letter-body p{margin-bottom:9px}
  .letter-footer{position:absolute;left:0;bottom:8px;width:100%;text-align:center;font-size:5px;line-height:7px;color:#fff;font-weight:300}
  .footer-mark{position:absolute;right:18px;bottom:22px;width:34px;height:34px;border-radius:50%;background:rgba(255,255,255,.85)}

  /* envelope */
  .envelope{left:498px;top:582px;width:413px;height:221px;border-radius:14px 14px 0 0}
  .envelope-flap{position:absolute;left:0;top:0;width:100%;height:46px;background:linear-gradient(90deg,var(--green-dark),var(--green-light) 50%,var(--green-dark))}
  .flap-mark{position:absolute;left:198px;top:14px;width:18px;height:18px;border-radius:50%;background:#fff}
  .envelope-band{position:absolute;left:0;top:46px;width:100%;height:8px;background:var(--band)}
  .envelope .brand{left:0;width:100%;justify-content:center;top:177px}
  .envelope .brand-dot{width:10px;height:10px}
  .envelope .brand-name{font-size:9px}
  .envelope-address{position:absolute;left:0;top:204px;width:100%;text-align:center;font-size:5.5px;font-weight:300;color:#666}
</style>
</head>
<body>

<!-- business card, front -->
<section class="piece card-front">
  <div class="brand"><span class="brand-dot"></span><span class="brand-name">Brookvale Poultry Pty Ltd</span></div>
  <svg class="wave" width="311" height="50" viewBox="0 0 311 50" preserveAspectRatio="none">
    <defs><linearGradient id="gCard" x1="0" x2="1"><stop offset="0" stop-color="#2e6a4c"/><stop offset=".6" stop-color="#5ea27e"/><stop offset="1" stop-color="#2e6a4c"/></linearGradient></defs>
    <path d="M0 4 C90 0 200 4 311 20 L311 50 L0 50 Z" fill="url(#gCard)"/>
    <path d="M0 22 C80 8 190 10 311 2 L311 50 L0 50 Z" fill="#2e6a4c" opacity=".75"/>
  </svg>
</section>

<!-- business card, back -->
<section class="piece card-back">
  <div class="brand"><span class="brand-dot"></span><span class="brand-name">Brookvale Poultry Pty Ltd</span></div>
  <div class="holder-name">Daniel Harper</div>
  <div class="holder-role">Director</div>
  <div class="card-address">
    <span class="label">Address</span> Old Mill Rd, KESTON SA 5120<br>
    Mailing Address: PO Box 212, ARLEN SA 5130
  </div>
  <div class="card-divider"></div>
  <div class="card-contact">
    Mob # 0400-123-456<br>
    Phone # 410-555-0192<br>
    Fax # 08-5550-1234<br>
    Email Id: d.harper@mailbox.example
  </div>
</section>

<!-- disc label -->
<section class="disc">
  <div class="brand"><span class="brand-dot"></span><span class="brand-name">Brookvale Poultry Pty Ltd</span></div>
  <svg class="wave" width="368" height="130" viewBox="0 0 368 130" preserveAspectRatio="none">
    <defs><linearGradient id="gDisc" x1="0" x2="1"><stop offset="0" stop-color="#2e6a4c"/><stop offset=".7" stop-color="#5ea27e"/><stop offset="1" stop-color="#2e6a4c"/></linearGradient></defs>
    <path d="M0 2 C120 -2 260 10 368 60 L368 130 L0 130 Z" fill="url(#gDisc)"/>
    <path d="M0 50 C110 18 250 20 368 0 L368 130 L0 130 Z" fill="#2e6a4c" opacity=".7"/>
  </svg>
  <div class="disc-hole"></div>
  <div class="disc-topic">Topic Name Here</div>
</section>

<!-- letterhead -->
<section class="piece letterhead">
  <div class="brand"><span class="brand-dot"></span><span class="brand-name">Brookvale Poultry Pty Ltd</span></div>
  <div class="header-rule"></div>
  <div class="letter-date">Date:______</div>
  <div class="letter-body">
    <p>Hello there,</p>
    <p>Thank you for your continued support this season. Our barns are running at full capacity and we expect steady supply through the coming months. Please find the updated delivery schedule attached for your review and records. Collection dates are listed by week, with quantities and barn numbers shown beside each entry.</p>
    <p>We have recently upgraded our feed storage and ventilation systems to improve bird welfare and meat quality. These changes may affect pickup times at the main gate, so please call ahead before arriving on site. Drivers should use the eastern entrance and follow the marked route to the loading bay.</p>
    <p>Our accounts team will send revised invoices at the end of each month. If you notice any differences in pricing or quantities, contact us and we will resolve them promptly. Payment terms remain thirty days from the date of issue.</p>
    <p>We look forward to working with you again this year and thank you for your ongoing partnership.</p>
    <p>Best regards,<br>Operations Office</p>
  </div>
  <svg class="wave" width="362" height="66" viewBox="0 0 362 66" preserveAspectRatio="none">
    <defs><linearGradient id="gLetter" x1="0" x2="1"><stop offset="0" stop-color="#2e6a4c"/><stop offset=".6" stop-color="#5ea27e"/><stop offset="1" stop-color="#2e6a4c"/></linearGradient></defs>
    <path d="M0 2 C110 -2 240 4 362 24 L362 66 L0 66 Z" fill="url(#gLetter)"/>
    <path d="M0 26 C100 8 230 10 362 0 L362 66 L0 66 Z" fill="#2e6a4c" opacity=".7"/>
  </svg>
  <div class="footer-mark"></div>
  <div class="letter-footer">
    Address: Old Mill Rd, KESTON SA 5120<br>
    Mailing Address: PO Box 212, ARLEN SA 5130<br>
    Phone # 0400-123-456 | Fax # 08-5550-1234 | Email Id: d.harper@mailbox.example
  </div>
</section>

<!-- envelope -->
<section class="piece envelope">
  <div class="envelope-flap"><span class="flap-mark"></span></div>
  <div class="envelope-band"></div>
  <div class="brand"><span class="brand-dot"></span><span class="brand-name">Brookvale Poultry Pty Ltd</span></div>
  <div class="envelope-address">Address: Old Mill Rd, KESTON SA 5120 &nbsp;|&nbsp; Mailing Address: PO Box 212, ARLEN SA 5130</div>
</section>

</body>
</html>
```